Bramblewood Card Company Business Cards

We are a trading card store with Glimmorax, sports and other TCG cards, we need a business card design that encompasses a clean cut, modern style with a retro flare. website is bramblewoodcardco.com for reference. Can utilize a comic book era feel or a more modern outdoor feel to utilize the "Pacific Northwest" elements of tress, mountains, etc.

Industry/Entity Type

Trading cards and collectibles

Contact Information for Business Card

business name, email address, phone number, name, owner job title

Font styles to use
Sans Serif

```html
<!DOCTYPE html>
<html lang="en">
<head>
<meta charset="utf-8">
<title>Bramblewood Card Company – Business Cards</title>
<link rel="stylesheet" href="https://fonts.googleapis.com/css2?family=Lato:wght@400;700;900&display=swap">
<style>
  :root {
    --stage: #3a3a3c;
    --card-dark: #050505;
    --card-light: #ffffff;
    --accent: #12b6d8;
    --slate: #6f6f72;
    --ink: #1c1c1c;
  }
  * { box-sizing: border-box; margin: 0; padding: 0; }
  html, body { width: 1200px; height: 689px; overflow: hidden; }
  body {
    background: var(--stage);
    font-family: "Lato", sans-serif;
    color: var(--ink);
    position: relative;
  }
  .card {
    position: absolute;
    top: 196px;
    width: 520px;
    height: 298px;
    border-radius: 22px;
  }
  .card--back { left: 40px; background: var(--card-dark); }
  .card--front { left: 640px; background: var(--card-light); }

  .wordmark {
    position: absolute;
    display: flex;
    align-items: center;
    gap: 12px;
  }
  .wordmark__dot {
    flex: none;
    border-radius: 50%;
    background: var(--accent);
  }
  .wordmark__name {
    font-weight: 900;
    text-transform: uppercase;
    line-height: 1.05;
    color: var(--slate);
    letter-spacing: 0.04em;
  }
  .card--back .wordmark {
    left: 50%; top: 50%;
    transform: translate(-50%, -50%);
  }
  .card--back .wordmark__dot { width: 44px; height: 44px; }
  .card--back .wordmark__name { font-size: 30px; color: #8a8a8d; }

  .card--front .wordmark { right: 34px; top: 38px; gap: 9px; }
  .card--front .wordmark__dot { width: 26px; height: 26px; }
  .card--front .wordmark__name { font-size: 17px; }

  .holder { position: absolute; left: 36px; top: 120px; }
  .holder__name {
    font-size: 27px;
    font-weight: 400;
    color: var(--accent);
    text-transform: uppercase;
    letter-spacing: 0.01em;
  }
  .holder__title { font-size: 16px; margin-top: 2px; }

  .divider {
    position: absolute;
    left: 36px; right: 34px; top: 190px;
    height: 1.5px;
    background: var(--ink);
  }

  .contact {
    position: absolute;
    left: 36px; top: 202px;
    list-style: none;
    font-size: 15px;
    line-height: 25px;
  }
  .contact li { display: flex; align-items: center; gap: 10px; }
  .contact svg { width: 15px; height: 15px; fill: var(--slate); flex: none; }

  .address {
    position: absolute;
    right: 34px; top: 204px;
    text-align: right;
    font-size: 15px;
    line-height: 22px;
  }
</style>
</head>
<body>
  <section class="card card--back" aria-label="Business card back">
    <div class="wordmark">
      <span class="wordmark__dot"></span>
      <span class="wordmark__name">Bramblewood<br>Card Company</span>
    </div>
  </section>

  <section class="card card--front" aria-label="Business card front">
    <div class="wordmark">
      <span class="wordmark__dot"></span>
      <span class="wordmark__name">Bramblewood<br>Card Company</span>
    </div>

    <div class="holder">
      <p class="holder__name">Dorian Vale</p>
      <p class="holder__title">Managing Director</p>
    </div>

    <div class="divider"></div>

    <ul class="contact">
      <li>
        <svg viewBox="0 0 16 16" aria-hidden="true"><path d="M3.5 1.5l2.6 3-1.4 1.7c.9 2 2.3 3.4 4.3 4.3l1.7-1.4 3 2.6-1.6 2.3C7 14 2 9 1.2 3.1z"/></svg>
        044-555 010 246
      </li>
      <li>
        <svg viewBox="0 0 16 16" aria-hidden="true"><path d="M1 3h14v10H1zM2.5 4.2L8 8.6l5.5-4.4z" fill-rule="evenodd"/></svg>
        info@bramblewoodcardco.com
      </li>
      <li>
        <svg viewBox="0 0 16 16" aria-hidden="true"><circle cx="8" cy="8" r="7"/><path d="M1 8h14M8 1c-2.5 2-2.5 12 0 14M8 1c2.5 2 2.5 12 0 14" stroke="#fff" stroke-width="1" fill="none"/></svg>
        www.bramblewoodcardco.com
      </li>
    </ul>

    <address class="address" style="font-style:normal">
      421, Address line goes here<br>
      45452, Country name
    </address>
  </section>
</body>
</html>
```